Need a business card design for a residential architect.

You can get a sense of his work at www.tberlove.com

Would like a consistent look and feel between business card and website
.

Target Market(s)

Residential homeowners builders

Industry/Entity Type

Residential

Contact Information for Business Card

Dale Morrick
Principle
Morrick Architecture
418 Kestrel Lane
Menlo Park, CA 94025

dale@tberlove.com

tberlove.com
phone: 650-555-2716
Fax: 650-555-8043

Font styles to use
Sans Serif

Requirements
Must have
• Details above
Nice to have
• Would like a consistent look and feel between business card and website
Should not have
• None

```html
<!DOCTYPE html>
<html lang="en">
<head>
<meta charset="utf-8">
<title>Morrick Architecture — Business Card</title>
<link rel="stylesheet" href="https://fonts.googleapis.com/css2?family=Montserrat:wght@400;500&display=swap">
<style>
  :root {
    --canvas: #ececec;
    --card-grey: #7a7a7a;
    --band-grey: #8c8c8c;
    --frame-light: #e4e4e4;
    --paper: #ffffff;
    --ink: #555555;
    --ink-light: #f4f4f4;
  }
  * { box-sizing: border-box; margin: 0; padding: 0; }
  html, body { width: 1200px; height: 988px; overflow: hidden; }
  body {
    background: var(--canvas);
    font-family: "Montserrat", sans-serif;
    position: relative;
  }
  .card {
    position: absolute;
    width: 520px;
    height: 297px;
    top: 345px;
    box-shadow: 0 6px 18px rgba(0,0,0,0.18);
    overflow: hidden;
  }

  /* Back side */
  .card-back {
    left: 50px;
    background: var(--frame-light);
    padding: 14px;
  }
  .card-back .face {
    width: 100%; height: 100%;
    display: flex; flex-direction: column;
  }
  .card-back .band { background: var(--band-grey); height: 62px; }
  .card-back .center {
    flex: 1; background: var(--paper);
    display: flex; align-items: center; justify-content: center;
  }

  /* Wordmark */
  .wordmark {
    color: var(--ink);
    font-weight: 400;
    text-align: center;
    line-height: 1;
  }
  .wordmark .name { display: block; font-size: 40px; letter-spacing: 1px; }
  .wordmark .sub { display: block; font-size: 11px; letter-spacing: 7.5px; margin-top: 6px; padding-left: 7px; }

  /* Front side */
  .card-front {
    left: 630px;
    background: var(--card-grey);
  }
  .card-front .logo-band {
    position: absolute;
    left: 32px; right: 24px; top: 22px; height: 134px;
    background: var(--paper);
    display: flex; align-items: center; justify-content: center;
  }
  .card-front .wordmark .name { font-size: 34px; }
  .card-front .wordmark .sub { font-size: 9.5px; letter-spacing: 6.5px; }
  .holder {
    position: absolute; left: 0; right: 0; top: 166px;
    text-align: center; color: var(--ink-light);
  }
  .holder .person { font-size: 12px; font-weight: 500; letter-spacing: 1px; }
  .holder .role { font-size: 8px; letter-spacing: 1px; margin-top: 2px; }
  .contacts {
    position: absolute; left: 72px; right: 40px; top: 206px;
    display: grid; grid-template-columns: 1fr 1fr; row-gap: 7px; column-gap: 14px;
    color: var(--ink-light); font-size: 8.5px;
  }
  .contacts .item { display: flex; align-items: center; gap: 6px; white-space: nowrap; }
  .contacts .wide { grid-column: 1 / 3; }
  .contacts svg { width: 11px; height: 11px; flex: none; }
  .rule { position: absolute; background: var(--paper); }
  .rule-right { right: 12px; top: 22px; bottom: 24px; width: 2px; }
  .rule-bottom { left: 160px; right: 12px; bottom: 24px; height: 2px; }
  .rule-bottom-thin { left: 160px; right: 12px; bottom: 19px; height: 1px; }
</style>
</head>
<body>

  <section class="card card-back" aria-label="Business card back">
    <div class="face">
      <div class="band"></div>
      <div class="center">
        <div class="wordmark">
          <span class="name">MORRICK</span>
          <span class="sub">ARCHITECTURE</span>
        </div>
      </div>
      <div class="band"></div>
    </div>
  </section>

  <section class="card card-front" aria-label="Business card front">
    <div class="logo-band">
      <div class="wordmark">
        <span class="name">MORRICK</span>
        <span class="sub">ARCHITECTURE</span>
      </div>
    </div>

    <div class="holder">
      <p class="person">DALE MORRICK</p>
      <p class="role">PRINCIPAL</p>
    </div>

    <div class="contacts">
      <div class="item">
        <svg viewBox="0 0 12 12" aria-hidden="true"><circle cx="6" cy="6" r="6" fill="#fff"/><path d="M4 3.2l1.1 1.3-.6.8c.4.8 1 1.4 1.8 1.8l.8-.6 1.3 1.1-.7.9C5.6 8.2 3.8 6.4 3.7 4z" fill="#7a7a7a"/></svg>
        <span>Phone: 650-555-2716</span>
      </div>
      <div class="item">
        <svg viewBox="0 0 12 12" aria-hidden="true"><circle cx="6" cy="6" r="6" fill="#fff"/><path d="M4 3.2l1.1 1.3-.6.8c.4.8 1 1.4 1.8 1.8l.8-.6 1.3 1.1-.7.9C5.6 8.2 3.8 6.4 3.7 4z" fill="#7a7a7a"/></svg>
        <span>Fax: 650-555-8043</span>
      </div>
      <div class="item">
        <svg viewBox="0 0 12 12" aria-hidden="true"><circle cx="6" cy="6" r="6" fill="#fff"/><rect x="3" y="4" width="6" height="4" fill="none" stroke="#7a7a7a" stroke-width=".8"/><path d="M3 4l3 2.2L9 4" fill="none" stroke="#7a7a7a" stroke-width=".8"/></svg>
        <span>dale@tberlove.com</span>
      </div>
      <div class="item">
        <svg viewBox="0 0 12 12" aria-hidden="true"><circle cx="6" cy="6" r="6" fill="#fff"/><circle cx="6" cy="6" r="3" fill="none" stroke="#7a7a7a" stroke-width=".8"/><path d="M3 6h6M6 3c-1.2 1.6-1.2 4.4 0 6M6 3c1.2 1.6 1.2 4.4 0 6" fill="none" stroke="#7a7a7a" stroke-width=".6"/></svg>
        <span>www.tberlove.com</span>
      </div>
      <div class="item wide">
        <svg viewBox="0 0 12 12" aria-hidden="true"><circle cx="6" cy="6" r="6" fill="#fff"/><path d="M6 9.5S3.8 6.8 3.8 5.2a2.2 2.2 0 0 1 4.4 0C8.2 6.8 6 9.5 6 9.5z" fill="#7a7a7a"/><circle cx="6" cy="5.2" r=".8" fill="#fff"/></svg>
        <span>418 Kestrel Lane, Menlo Park, CA 94025</span>
      </div>
    </div>

    <div class="rule rule-right"></div>
    <div class="rule rule-bottom"></div>
    <div class="rule rule-bottom-thin"></div>
  </section>

</body>
</html>
```